Hallowell Kin Playing Cards

We are wanting a cool design for a playing card that includes our logo(s). I will attach our two logos, we are open to using either one of them or another version of them. I will also attach some pictures of card decks to use for inspiration. These are just decks that we have seen from other artists that we liked. We are located in West Texas so although not necessary, a Sotol or Agave or cactus or quail (bird) or some sort of sunset would pay homage to our surroundings. I realize the examples are all very different, but those are just some decks that we like! Thank you!

```html
<!DOCTYPE html>
<html lang="en">
<head>
<meta charset="utf-8">
<title>Hallowell Kin Playing Cards — Ace and Card Back</title>
<link href="https://fonts.googleapis.com/css2?family=Rye&display=swap" rel="stylesheet">
<style>
  :root {
    --page-bg: #eeeff1;
    --card-blue: #163c93;
    --panel-blue: #0f2c74;
    --deep-navy: #0b1c4f;
    --sun-gold: #f0b323;
    --pale-gold: #f4dd8a;
    --sunset-orange: #ec7f26;
    --dusk-purple: #2b2670;
    --suit-black: #060606;
    --line-white: #ffffff;
  }
  * { box-sizing: border-box; margin: 0; padding: 0; }
  html, body {
    width: 1200px;
    height: 933px;
    overflow: hidden;
    background: var(--page-bg);
  }
  .deck-display {
    width: 1200px;
    height: 933px;
    display: flex;
    justify-content: center;
    align-items: center;
    gap: 90px;
  }
  .playing-card {
    width: 400px;
    height: 560px;
    border-radius: 24px;
    overflow: hidden;
    box-shadow: 0 18px 40px rgba(20, 30, 60, 0.18);
  }
  .playing-card svg { display: block; }
  .card-index {
    font-family: "Rye", "Georgia", serif;
    font-size: 60px;
    fill: var(--suit-black);
    stroke: var(--line-white);
    stroke-width: 2.5px;
    paint-order: stroke;
  }
</style>
</head>
<body>
<main class="deck-display">

  <article class="playing-card ace-face" aria-label="Ace of spades">
    <svg width="400" height="560" viewBox="0 0 400 560" xmlns="http://www.w3.org/2000/svg">
      <defs>
        <linearGradient id="ace-border" x1="1" y1="0" x2="0" y2="1">
          <stop offset="0" stop-color="var(--card-blue)"/>
          <stop offset="0.55" stop-color="var(--card-blue)"/>
          <stop offset="0.75" stop-color="var(--pale-gold)"/>
          <stop offset="1" stop-color="var(--sun-gold)"/>
        </linearGradient>
      </defs>
      <rect class="card-base" width="400" height="560" rx="24" fill="url(#ace-border)"/>

      <path class="center-panel"
            d="M112 34 H372 V470 H300 Q288 470 288 482 V528 H28 V124 H100 Q112 124 112 112 Z"
            fill="var(--panel-blue)" stroke="var(--line-white)" stroke-width="1.2"/>

      <g class="corner-circle" stroke="var(--line-white)" fill="var(--deep-navy)" stroke-width="1.5">
        <circle cx="362" cy="80" r="18"/>
        <circle cx="38" cy="480" r="18"/>
      </g>

      <g class="index-top">
        <text class="card-index" x="70" y="82" text-anchor="middle">A</text>
        <path d="M70 92 C78 102 88 108 88 116 C88 123 80 126 73 121 L76 130 H64 L67 121 C60 126 52 123 52 116 C52 108 62 102 70 92 Z"
              fill="var(--suit-black)" stroke="var(--line-white)" stroke-width="2"/>
      </g>
      <g class="index-bottom" transform="rotate(180 330 500)">
        <text class="card-index" x="330" y="500" text-anchor="middle">A</text>
        <path d="M330 510 C338 520 348 526 348 534 C348 541 340 544 333 539 L336 548 H324 L327 539 C320 544 312 541 312 534 C312 526 322 520 330 510 Z"
              fill="var(--suit-black)" stroke="var(--line-white)" stroke-width="2"/>
      </g>

      <rect class="center-pip" role="img" aria-label="Large stylised spade pip with a small star"
            x="110" y="170" width="180" height="200" rx="20" fill="var(--suit-black)"/>
    </svg>
  </article>

  <article class="playing-card card-back" aria-label="Card back">
    <svg width="400" height="560" viewBox="0 0 400 560" xmlns="http://www.w3.org/2000/svg">
      <defs>
        <linearGradient id="sunset-scene" x1="0" y1="0" x2="0" y2="1">
          <stop offset="0" stop-color="#2a56a8"/>
          <stop offset="0.3" stop-color="#7fa6d0"/>
          <stop offset="0.45" stop-color="var(--pale-gold)"/>
          <stop offset="0.6" stop-color="var(--sunset-orange)"/>
          <stop offset="0.75" stop-color="var(--dusk-purple)"/>
          <stop offset="1" stop-color="#0a0a1e"/>
        </linearGradient>
      </defs>
      <rect class="card-base" width="400" height="560" rx="24" fill="var(--card-blue)"/>
      <rect class="outer-frame" x="20" y="20" width="360" height="520" rx="10" fill="none" stroke="var(--line-white)" stroke-width="1.3"/>
      <rect class="scene-window" role="img" aria-label="West Texas sunset with a rider on horseback, cacti and birds"
            x="34" y="34" width="332" height="492" rx="16" fill="url(#sunset-scene)" stroke="var(--line-white)" stroke-width="1.3"/>

      <g class="corner-circle" stroke="var(--line-white)" fill="var(--deep-navy)" stroke-width="1.5">
        <circle cx="366" cy="90" r="18"/>
        <circle cx="34" cy="470" r="18"/>
      </g>
    </svg>
  </article>

</main>
</body>
</html>
```